Storm Restoration Contractor needs a professional letterhead design

Looking for a professional letterhead design. Not looking for your cheapo MS Word standard ones that are readily available. Dont want it to be cookie cutter look like ones readily available online. We just recently changed our logo and want to freshen up all our documents. Our company handles restoring a property back to a pre-loss condition after a storm damages it. For example, wind, hail, flood, fire losses.

Target Market(s)

Property Owners, Homeowners, Property Owners, Commercial Property Owners, Property Management Companies

Industry/Entity Type

Construction Company

Requirements
Must have
• Professional, Use 1 of 2 logo options
• Storm Restoration, Roofing, Siding, Windows

```html
<!DOCTYPE html>
<html lang="en">
<head>
<meta charset="utf-8">
<title>Stormline Exteriors Letterhead</title>
<link href="https://fonts.googleapis.com/css2?family=PT+Sans:wght@400;700&display=swap" rel="stylesheet">
<style>
  :root {
    --backdrop: #e9eaec;
    --paper: #ffffff;
    --brand-blue: #1f78c3;
    --brand-grey: #55585c;
    --ink: #3d4044;
    --watermark: #eef1f7;
    --on-blue: #ffffff;
  }
  * { box-sizing: border-box; margin: 0; padding: 0; }
  html, body {
    width: 1200px;
    height: 795px;
    overflow: hidden;
    background: var(--backdrop);
    font-family: "PT Sans", sans-serif;
  }
  .canvas {
    width: 1200px;
    height: 795px;
    display: flex;
    align-items: center;
    justify-content: center;
  }
  .letterhead {
    position: relative;
    width: 524px;
    height: 741px;
    background: var(--paper);
    overflow: hidden;
    box-shadow: 0 2px 10px rgba(0,0,0,0.08);
  }
  address { font-style: normal; }
  .brand {
    position: absolute;
    top: 46px;
    left: 38px;
    display: flex;
    align-items: center;
    gap: 8px;
  }
  .brand-dot {
    width: 26px;
    height: 26px;
    border-radius: 50%;
    background: var(--brand-blue);
  }
  .brand-name {
    font-weight: 700;
    font-size: 13px;
    letter-spacing: 1.5px;
    text-transform: uppercase;
    color: var(--brand-blue);
  }
  .contact {
    position: absolute;
    top: 44px;
    right: 38px;
    text-align: right;
    font-size: 8.5px;
    line-height: 1.45;
    color: var(--ink);
  }
  .contact-row {
    display: flex;
    justify-content: flex-end;
    align-items: center;
    gap: 6px;
  }
  .social {
    display: flex;
    gap: 3px;
  }
  .social span {
    width: 7px;
    height: 7px;
    border-radius: 50%;
    background: var(--brand-blue);
  }
  .watermark {
    position: absolute;
    top: 190px;
    left: 112px;
    width: 300px;
    height: 300px;
    border: 18px solid var(--watermark);
    border-radius: 50%;
    display: flex;
    align-items: center;
    justify-content: center;
  }
  .watermark-name {
    font-weight: 700;
    font-size: 30px;
    line-height: 1.1;
    text-align: center;
    text-transform: uppercase;
    letter-spacing: 2px;
    color: var(--watermark);
  }
  .footer-wave {
    position: absolute;
    left: 0;
    bottom: 0;
    width: 524px;
    height: 260px;
  }
  .footer-address {
    position: absolute;
    left: 38px;
    bottom: 22px;
    font-size: 10px;
    line-height: 1.35;
    color: var(--on-blue);
  }
</style>
</head>
<body>
  <main class="canvas">
    <section class="letterhead">
      <header class="brand">
        <span class="brand-dot"></span>
        <span class="brand-name">Stormline Exteriors</span>
      </header>

      <address class="contact">
        <div class="contact-row">
          <span>(555) 214-0387</span>
          <span class="social"><span></span><span></span><span></span><span></span></span>
        </div>
        <div>(555) 214-0388</div>
        <div>info@stormlineexteriors.com</div>
        <div>www.stormlineexteriors.com</div>
      </address>

      <div class="watermark" aria-hidden="true">
        <span class="watermark-name">Stormline<br>Exteriors</span>
      </div>

      <svg class="footer-wave" viewBox="0 0 524 260" preserveAspectRatio="none" aria-hidden="true">
        <path fill="var(--brand-blue)" d="M0 160 C110 135 230 140 290 110 C360 75 400 15 524 0 L524 260 L0 260 Z"/>
        <path fill="var(--brand-grey)" d="M0 178 C110 152 240 158 300 125 C370 88 420 32 524 18 L524 260 L0 260 Z"/>
        <path fill="var(--brand-blue)" d="M0 196 C120 172 250 180 320 140 C390 100 440 58 524 46 L524 260 L0 260 Z"/>
      </svg>

      <address class="footer-address">
        <div>Stormline Exteriors</div>
        <div>2270 Harbor Park Drive, Riverton, CA 95012</div>
      </address>
    </section>
  </main>
</body>
</html>
```